Garlic Farm for Farm Sales/Restaurant sales

Need a professional, but appealing to agriculture world. We are selling 27 kinds of Organic Garlic from a farm in Simla,CO. I have uploaded logo and business information-we are going to need a template, because I will need to use it for four separate people.
-We are trying to appeal to Farm to table restaurants
-As well as growers/farmers

Target Market(s)

Agriculture Sales/Restaurants-Organic

Industry/Entity Type

Agriculture

Contact Information for Business Card

Want it to look more unique then your average kelto stock card- I want it to look amazing

Font styles to use
Sans Serif

Colors
0455a3
ec1f27
fbed22
ffffff

Requirements
Must have
• Just be creative
Nice to have
• Colorful
Should not have
• plain

```html
<!DOCTYPE html>
<html lang="en">
<head>
<meta charset="utf-8">
<title>Summit Ridge Garlic – Business Card</title>
<link href="https://fonts.googleapis.com/css2?family=Open+Sans:wght@400;600;700&display=swap" rel="stylesheet">
<style>
  :root {
    --navy: #0f3b6e;
    --crimson: #c00a2f;
    --gold: #fdd800;
    --gold-deep: #f4c400;
    --paper: #ffffff;
    --ink: #4a4a4a;
    --rule: #2b2b2b;
    --backdrop: #e7e3de;
  }
  * { margin: 0; padding: 0; box-sizing: border-box; }
  html, body { width: 1200px; height: 987px; overflow: hidden; }
  body {
    background: var(--backdrop);
    font-family: "Open Sans", Arial, sans-serif;
    position: relative;
  }
  .card {
    position: absolute;
    left: 293px;
    width: 615px;
    height: 350px;
    overflow: hidden;
  }
  .card--front { top: 130px; background: var(--paper); }
  .card--back { top: 506px; background: var(--crimson); }

  /* Front: brand lockup */
  .brand {
    position: absolute;
    left: 0; right: 0;
    top: 62px;
    display: flex;
    justify-content: center;
    align-items: center;
    gap: 16px;
  }
  .brand-dot {
    width: 58px;
    height: 58px;
    border-radius: 50%;
    background: var(--crimson);
    flex: none;
  }
  .brand-name {
    color: var(--navy);
    font-weight: 700;
    font-size: 38px;
    line-height: 1.05;
    letter-spacing: 0.3px;
  }
  .tagline {
    position: absolute;
    left: 0; right: 0;
    top: 150px;
    text-align: center;
    color: var(--crimson);
    font-size: 15px;
    font-weight: 600;
    letter-spacing: 3px;
  }

  .divider {
    position: absolute;
    left: 26px; right: 29px;
    top: 244px;
    height: 1px;
    background: var(--rule);
  }
  .person { position: absolute; left: 26px; top: 253px; }
  .person-name { color: var(--navy); font-weight: 600; font-size: 22px; line-height: 30px; }
  .person-role { color: var(--crimson); font-size: 16px; line-height: 22px; }
  .person-email { color: var(--ink); font-size: 16px; line-height: 22px; margin-top: 8px; }

  .contact {
    position: absolute;
    right: 29px;
    top: 251px;
    text-align: right;
    color: var(--ink);
    font-size: 16px;
    line-height: 26px;
  }
  .contact-line { display: flex; justify-content: flex-end; align-items: center; gap: 8px; }
  .contact-line svg { width: 15px; height: 15px; fill: var(--navy); }

  /* Back */
  .bulb-art {
    position: absolute;
    left: 0;
    top: 0;
    width: 340px;
    height: 350px;
    background:
      radial-gradient(ellipse 62% 58% at 48% 60%, var(--gold) 0%, var(--gold-deep) 45%, rgba(192,10,47,0) 78%);
  }
  .back-brand {
    position: absolute;
    left: 350px;
    right: 24px;
    top: 222px;
    color: var(--paper);
    font-weight: 700;
    font-size: 28px;
    line-height: 1.15;
    text-align: center;
  }
  .back-tagline {
    position: absolute;
    left: 350px;
    right: 24px;
    top: 292px;
    text-align: center;
    color: var(--paper);
    font-size: 14px;
    font-weight: 600;
    letter-spacing: 3px;
  }
</style>
</head>
<body>
  <section class="card card--front">
    <div class="brand">
      <span class="brand-dot"></span>
      <span class="brand-name">Summit Ridge Garlic</span>
    </div>
    <div class="tagline">GOURMET GARLIC</div>
    <div class="divider"></div>
    <div class="person">
      <div class="person-name">DALE WHITFORD</div>
      <div class="person-role">CEO/FOUNDER</div>
      <div class="person-email">dale@srgarlic.com</div>
    </div>
    <div class="contact">
      <div class="contact-line">555-014-2273
        <svg viewBox="0 0 24 24" aria-hidden="true"><path d="M6.6 10.8a15.2 15.2 0 0 0 6.6 6.6l2.2-2.2c.3-.3.7-.4 1-.2 1.1.4 2.3.6 3.6.6.6 0 1 .4 1 1V20c0 .6-.4 1-1 1A17 17 0 0 1 3 4c0-.6.4-1 1-1h3.5c.6 0 1 .4 1 1 0 1.3.2 2.5.6 3.6.1.3 0 .7-.2 1z"/></svg>
      </div>
      <div class="contact-line">www.SRGarlic.com
        <svg viewBox="0 0 24 24" aria-hidden="true"><circle cx="12" cy="12" r="10"/><path d="M2 12h20M12 2c3 3 3 17 0 20M12 2c-3 3-3 17 0 20" stroke="#fff" stroke-width="1.6" fill="none"/></svg>
      </div>
      <div class="contact-line">P.O. Box 48 Larkin, CO&nbsp; 80000</div>
    </div>
  </section>

  <section class="card card--back">
    <div class="bulb-art" role="img" aria-label="Large illustrated yellow garlic bulb with navy outlines"></div>
    <div class="back-brand">Summit Ridge Garlic</div>
    <div class="back-tagline">GOURMET GARLIC</div>
  </section>
</body>
</html>
```